Design for schnapps bottle label "Río Ámbar"

Hi! On a small land lot we are producing our own Italian schnapps "Grappa". For the bottles we would like to modernize our current labes that you find below. The two cats looking at each other should remain, but updated and more modern. I am very much looking forward to your suggestions. Best, Jens

Target Market(s)

Schnapps bottle label

Requirements
Must have
• Cats should resemble the cats that are decorating the house entry (see attached), however, should have a more modern appearance.

Text elements should remain: "Grappa", "Río Ámbar", "Legnoso", "[Vintage Year], "Raccolta No", "Vol %"
Should not have
• Current ornament can be used, replaced or deleted (whatever looks best)

```html
<!DOCTYPE html>
<html lang="it">
<head>
<meta charset="utf-8">
<title>Grappa – Río Ámbar label</title>
<link rel="stylesheet" href="https://fonts.googleapis.com/css2?family=Federo&family=Cormorant+Garamond:wght@500;600&display=swap">
<style>
  :root {
    --backdrop: #bdb8b2;
    --label-paper: #ffffff;
    --ink: #141414;
    --ink-soft: #2b2b2b;
    --ornament-tone: #3a3a3a;
  }
  * { margin: 0; padding: 0; box-sizing: border-box; }
  html, body {
    width: 1200px;
    height: 960px;
    overflow: hidden;
    background: var(--backdrop);
  }
  .label {
    position: absolute;
    left: 322px;
    top: 73px;
    width: 556px;
    height: 814px;
    background: var(--label-paper);
    color: var(--ink);
  }
  .label__ornament {
    position: absolute;
    left: 330px;
    top: 48px;
    width: 190px;
    height: 50px;
    background: linear-gradient(180deg, #ffffff 0%, var(--ornament-tone) 50%, #ffffff 100%);
    opacity: 0.55;
  }
  .label__title {
    position: absolute;
    left: 22px;
    top: 92px;
    font-family: "Federo", sans-serif;
    font-size: 148px;
    line-height: 1;
    font-weight: 400;
    letter-spacing: -2px;
  }
  .label__rule {
    position: absolute;
    left: 62px;
    top: 246px;
    width: 478px;
    height: 3px;
    background: var(--ink);
  }
  .label__cuvee {
    position: absolute;
    left: 0;
    width: 100%;
    top: 312px;
    text-align: center;
    font-family: "Federo", sans-serif;
    font-size: 54px;
    line-height: 1;
  }
  .label__cuvee-name { margin-right: 14px; }
  .label__by {
    position: absolute;
    left: 0;
    width: 100%;
    top: 376px;
    text-align: center;
    font-family: "Federo", sans-serif;
    font-size: 54px;
    line-height: 1;
  }
  .label__cats {
    position: absolute;
    left: 0;
    top: 524px;
    width: 100%;
    height: 124px;
  }
  .label__producer {
    position: absolute;
    left: 0;
    width: 100%;
    top: 694px;
    text-align: center;
    font-family: "Federo", sans-serif;
    font-size: 44px;
    line-height: 1;
    letter-spacing: 2px;
  }
  .label__footer {
    position: absolute;
    left: 0;
    right: 0;
    top: 754px;
    display: flex;
    justify-content: space-between;
    font-family: "Cormorant Garamond", serif;
    font-weight: 600;
    font-size: 26px;
    color: var(--ink-soft);
    padding: 0 4px;
  }
</style>
</head>
<body>
  <main class="label">
    <div class="label__ornament" role="img" aria-label="Decorative scroll ornament above the title"></div>
    <h1 class="label__title">Grappa</h1>
    <div class="label__rule"></div>
    <p class="label__cuvee"><span class="label__cuvee-name">“legnoso”</span><span class="label__vintage">2015</span></p>
    <p class="label__by">di</p>
    <svg class="label__cats" viewBox="0 0 556 124" role="img" aria-label="Two stretching black cat silhouettes facing each other">
      <rect x="84" y="0" width="134" height="124" rx="30" fill="#161616"/>
      <rect x="336" y="0" width="134" height="124" rx="30" fill="#161616"/>
    </svg>
    <p class="label__producer">Río Ámbar</p>
    <div class="label__footer">
      <span class="label__batch">Raccolta No. 01</span>
      <span class="label__abv">41,0% Vol</span>
    </div>
  </main>
</body>
</html>
```